Investment company needing business card

We are wanting a business card which looks sharp and easy on the eye. We are thinking of having a business card with the logo embossed on it, to really make it stand out. We will only have a small amount of information of the business card, person's name, position, email address and phone number

Contact Information for Business Card

Danielle Frost
Executive Assistant
+64 21 473 5162
danielf@harwickpartners.co.nz

Requirements
Must have
• Embossed logo
Should not have
• Not to be busy

```html
<!DOCTYPE html>
<html lang="en">
<head>
<meta charset="utf-8">
<title>Harwick Partners – Business Card</title>
<link href="https://fonts.googleapis.com/css2?family=Roboto+Condensed:wght@300;400;500&display=swap" rel="stylesheet">
<style>
  :root {
    --backdrop: #e9e7e3;
    --card: #fbfbfb;
    --teal: #3ec8a2;
    --ink: #6e6e6e;
    --ink-soft: #8a8a8a;
  }
  * { margin: 0; padding: 0; box-sizing: border-box; }
  html, body {
    width: 1200px;
    height: 1023px;
    overflow: hidden;
    background: var(--backdrop);
    font-family: "Roboto Condensed", Arial, sans-serif;
  }
  .canvas {
    position: relative;
    width: 1200px;
    height: 1023px;
    display: flex;
    align-items: center;
    justify-content: center;
  }
  .business-card {
    position: relative;
    width: 900px;
    height: 514px;
    background: linear-gradient(135deg, #ffffff 0%, var(--card) 55%, #f0f0f0 100%);
    border-radius: 22px;
    box-shadow: 0 18px 40px rgba(0,0,0,0.12), 0 2px 6px rgba(0,0,0,0.08);
    display: flex;
    align-items: center;
  }
  .brand {
    position: absolute;
    left: 90px;
    top: 50%;
    transform: translateY(-50%);
    display: flex;
    align-items: center;
    gap: 16px;
  }
  .brand-square {
    width: 46px;
    height: 46px;
    background: var(--teal);
  }
  .brand-name {
    font-size: 34px;
    font-weight: 500;
    letter-spacing: 2px;
    color: var(--teal);
    line-height: 1;
  }
  .divider {
    position: absolute;
    left: 470px;
    top: 50%;
    width: 1px;
    height: 170px;
    transform: translateY(-50%);
    background: var(--teal);
  }
  .contact {
    position: absolute;
    left: 510px;
    top: 50%;
    transform: translateY(-50%);
  }
  .person-name {
    font-size: 38px;
    font-weight: 400;
    letter-spacing: 1px;
    color: var(--teal);
    line-height: 1;
  }
  .person-role {
    margin-top: 8px;
    font-size: 19px;
    font-weight: 300;
    color: var(--ink-soft);
  }
  .dash {
    width: 14px;
    height: 1px;
    background: var(--teal);
    margin: 16px 0 14px;
  }
  .detail-list { list-style: none; }
  .detail {
    display: flex;
    align-items: center;
    gap: 12px;
    font-size: 18px;
    font-weight: 300;
    color: var(--ink);
    line-height: 28px;
  }
  .detail svg { width: 13px; height: 13px; flex: none; }
</style>
</head>
<body>
<main class="canvas">
  <article class="business-card">
    <div class="brand">
      <span class="brand-square"></span>
      <span class="brand-name">HARWICK PARTNERS</span>
    </div>

    <span class="divider"></span>

    <section class="contact">
      <h1 class="person-name">DANIELLE FROST</h1>
      <p class="person-role">Executive Assistant</p>
      <div class="dash"></div>
      <ul class="detail-list">
        <li class="detail">
          <svg viewBox="0 0 16 16" aria-hidden="true"><path d="M4 1.5l2.5 3-1.5 1.8c.9 1.9 2.3 3.3 4.2 4.2L11 9l3 2.5-1.4 2.4C7.5 13.6 2.4 8.5 1.6 3z" fill="var(--teal)"/></svg>
          +64 21 473 5162
        </li>
        <li class="detail">
          <svg viewBox="0 0 16 16" aria-hidden="true"><rect x="1.5" y="3.5" width="13" height="9" fill="none" stroke="var(--teal)" stroke-width="1.4"/><path d="M1.5 3.5L8 9l6.5-5.5" fill="none" stroke="var(--teal)" stroke-width="1.4"/></svg>
          danielf@harwickpartners.co.nz
        </li>
        <li class="detail">
          <svg viewBox="0 0 16 16" aria-hidden="true"><circle cx="8" cy="8" r="6.5" fill="none" stroke="var(--teal)" stroke-width="1.4"/><ellipse cx="8" cy="8" rx="2.8" ry="6.5" fill="none" stroke="var(--teal)" stroke-width="1.1"/><path d="M1.5 8h13" stroke="var(--teal)" stroke-width="1.1"/></svg>
          www.harwickpartners.co.nz
        </li>
      </ul>
    </section>
  </article>
</main>
</body>
</html>
```